Blog Design for global news commentary

Need a very simple blog template (see attachment, Frontpage) that includes entries and ability to upload photos/video. Tabs are not needed (See Marlow Tearoom Provincial blog for sort of what I am going for but a lot less cluttered). A section that can access old entries is needed as well as a "contact me" tab. The format should be very simple. An entry and section for comments, new entry, section for comments etc. comments sections should be able to be monitored by me. With the ability for readers to contribute via quidlane. The look and feel should be sophisticated and should target an educated global audience. The blog is all about commenting on global news around the world. For example, a news article could be photographed and then commented on. Type face should be simple, clean and 1930's style. See Harbor Ledger magazine for looks and feel. If viewers wish to contribute they can make donations via quidlane on the site. Once the template is competed it should be very easy for me to update and work with and handed over to a web hosting service. I own the domain name which I want to use. It would be best to use an existing template eg wordpress. So in simple terms need a wordpress template adapted for this blog idea. Not sure what coded vs. uncoded means. But the overall objective is very simple. Template should be clean, no design elements other than the name of the blog.

Target Market(s)

Educated people from around the world interested in current events

Industry/Entity Type

News

Number of Pages Required

2 page

Other font styles liked:
• Upper East Side

Colors
0255a3
1b1b1b
5c5c5c

Requirements
Must have
• This is a blog so it should have all the standard features including daily updates, photo/video upload, comments that can be monitored by me, quidlane donation link. It should be easy for me to use and handle once completed and delivered to web host. It must have a simple, elegant look and feel. I have chose Serif font style but recommend a 1930's Art Deco - clean, unfussy type face. Type face Upper East Side is what I am looking for
Nice to have
• The look must be simple and no pictures, design elements or logos. Clean and crisp
Should not have
• Any pictures for illustrations as part of the overall design

```html
<!DOCTYPE html>
<html lang="en">
<head>
<meta charset="utf-8">
<title>Vantmere — Global News Around the World</title>
<link href="https://fonts.googleapis.com/css2?family=Roboto:wght@400;500;700;900&family=Playfair+Display:wght@700&display=swap" rel="stylesheet">
<style>
:root{
  --blue:#0255a3;
  --ink:#1b1b1b;
  --grey:#5c5c5c;
  --light:#8a8a8a;
  --rule:#e2e2e2;
  --page:#e6e6e6;
  --white:#ffffff;
  --deep:#121212;
  --red:#d8262b;
}
*{box-sizing:border-box;margin:0;padding:0}
html,body{width:1200px;height:2768px;overflow:hidden}
body{background:var(--page);font-family:"Roboto",Arial,sans-serif;color:var(--ink);position:relative}
.abs{position:absolute}
.photo{display:block}

/* header */
.topbar{left:60px;top:0;width:1080px;height:120px;background:var(--ink)}
.brand{position:absolute;left:30px;top:34px;font-family:"Playfair Display",Georgia,serif;font-weight:700;font-size:40px;color:var(--white);letter-spacing:1px}
.login{position:absolute;left:680px;top:42px;width:104px;height:34px;border:1px solid #444;border-radius:3px;color:#ddd;font-size:12px;display:flex;align-items:center;justify-content:center;gap:8px;background:#262626}
.connect{position:absolute;right:24px;top:46px;display:flex;align-items:center;gap:8px;color:#ccc;font-size:12px}
.connect .label{margin-right:8px}
.social-dot{width:26px;height:26px;border-radius:50%;background:#3a3a3a;display:block}

.mainnav{left:60px;top:120px;width:1080px;height:48px;background:var(--blue);display:flex;align-items:center}
.mainnav ul{display:flex;list-style:none;height:100%}
.mainnav li{height:100%;display:flex;align-items:center;padding:0 19px;color:var(--white);font-size:12px;font-weight:700;letter-spacing:.5px}
.mainnav li.active{background:#013f7a}
.donate{position:absolute;left:844px;top:7px;width:168px;height:34px;background:var(--white);border-radius:3px;display:flex;flex-direction:column;align-items:center;justify-content:center;line-height:1.1}
.donate small{font-size:9px;color:var(--grey)}
.donate strong{font-size:14px;color:var(--blue);font-weight:700}
.search{position:absolute;right:6px;top:7px;width:40px;height:34px;background:#f1c40f;border-radius:3px;display:flex;align-items:center;justify-content:center}

/* hero */
.hero{left:60px;top:168px;width:1080px;height:424px;overflow:hidden}
.hero .photo{width:100%;height:100%;background:linear-gradient(120deg,#0b1a2c 0%,#1f4e6e 38%,#4b8fb0 58%,#1a3148 80%,#0a1420 100%)}
.hero-caption{position:absolute;left:0;bottom:26px;background:rgba(10,20,30,.85);color:var(--white);font-size:12px;font-weight:700;padding:12px 22px;letter-spacing:.4px}
.hero-dots{position:absolute;right:30px;bottom:32px;display:flex;gap:8px}
.hero-dots span{width:9px;height:9px;border-radius:50%;background:rgba(255,255,255,.5)}
.hero-dots span:first-child{background:var(--white)}
.hero-arrow{position:absolute;top:190px}

/* panel */
.panel{left:60px;top:600px;width:1080px;height:1860px;background:var(--white)}
.section-head{position:absolute;height:30px;border-bottom:2px solid var(--blue)}
.section-head span{display:inline-block;height:30px;line-height:30px;padding:0 16px;background:var(--blue);color:var(--white);font-size:12px;font-weight:700;letter-spacing:.6px}
.section-head.side span{background:var(--white);color:var(--ink);border-left:4px solid var(--blue);padding-left:10px}

.headline{font-weight:700;text-transform:uppercase;color:var(--ink);letter-spacing:.2px}
.meta{font-size:10px;color:var(--light);display:flex;gap:12px;align-items:center}
.body-text{font-size:11px;line-height:18px;color:var(--grey)}
.more{font-size:10px;font-weight:700;color:var(--ink);text-transform:uppercase}
.tag{display:inline-block;background:var(--blue);color:var(--white);font-size:9px;font-weight:700;padding:5px 9px;letter-spacing:.4px;text-transform:uppercase}

/* news */
.feature{left:12px;top:88px;width:368px}
.feature .photo{width:368px;height:320px;position:relative;background:linear-gradient(160deg,#c9c9c5 0%,#8a8f96 45%,#3d4650 100%)}
.play{position:absolute;left:152px;top:128px}
.feature .headline{font-size:13px;line-height:19px;margin-top:16px}
.feature .meta{margin-top:10px}
.feature .body-text{margin-top:12px}
.feature .more{margin-top:16px;display:block}

.news-list{left:400px;top:100px;width:340px;list-style:none}
.news-list li{display:flex;gap:14px;height:108px}
.thumb{width:72px;height:72px;flex:none}
.news-list .headline{font-size:11px;line-height:16px}
.news-list .meta{margin-top:8px}

/* articles */
.articles{left:12px;top:740px;width:728px;display:flex;gap:13px}
.article-card{position:relative;width:172px;height:188px}
.article-card .photo{width:100%;height:100%}
.article-card .overlay{position:absolute;left:10px;bottom:14px;right:10px}
.article-card .headline{color:var(--white);font-size:10px;line-height:14px;margin-top:8px}

/* latest */
.latest-main{left:12px;top:1080px;width:368px;height:232px;background:linear-gradient(150deg,#dfe3e6 0%,#9aa4ad 50%,#4e5861 100%)}
.latest-copy{left:400px;top:1080px;width:340px}
.latest-copy .headline{font-size:14px;line-height:20px;margin-top:12px}
.latest-copy .meta{margin-top:8px}
.latest-copy .body-text{margin-top:12px}
.latest-copy .more{margin-top:14px;display:block}
.latest-small{top:1348px;display:flex;gap:14px}
.latest-small .photo{flex:none}
.latest-small .headline{font-size:11px;line-height:16px}
.latest-small .body-text{font-size:10px;line-height:15px;margin-top:4px}
.latest-small .meta{margin-top:6px}

/* sidebar */
.trending{left:784px;top:96px;width:288px;list-style:none}
.trending li{display:flex;gap:12px;height:58px;padding-top:6px;border-bottom:1px solid var(--rule)}
.trending li+li{padding-top:10px}
.bullet{width:16px;height:16px;border-radius:50%;background:var(--blue);flex:none;margin-top:2px}
.trending .headline{font-size:10px;line-height:15px}

.recent{left:784px;top:640px;width:288px;list-style:none}
.recent li{display:flex;gap:12px;height:74px}
.recent .thumb{width:56px;height:56px}
.recent .headline{font-size:10px;line-height:15px}
.recent .meta{margin-top:6px}

.side-card{left:784px;width:288px}
.side-card .photo{width:288px;position:relative}
.side-card .tag{position:absolute;left:10px;top:10px}
.side-card .headline{font-size:11px;line-height:16px;margin-top:12px}
.side-card .meta{margin-top:6px}

/* gallery */
.gallery{left:12px;top:1584px;width:1060px;display:flex;gap:14px}
.gallery figure{position:relative;width:344px;height:262px}
.gallery .photo{width:100%;height:100%}
.gallery figcaption{position:absolute;left:16px;bottom:18px;right:16px}
.gallery .headline{color:var(--white);font-size:13px;line-height:18px;margin-top:8px}

/* newsletter */
.newsletter{left:60px;top:2480px;width:1080px;height:160px;background:var(--ink);text-align:center;padding-top:40px}
.newsletter h2{color:var(--white);font-size:13px;font-weight:700;letter-spacing:1px}
.subscribe{display:flex;justify-content:center;margin-top:24px}
.subscribe .field{width:500px;height:40px;background:#2c2c2c;border:1px solid #3c3c3c;display:flex;align-items:center;gap:10px;padding-left:14px;color:#888;font-size:11px}
.subscribe .go{width:44px;height:40px;background:var(--blue);display:flex;align-items:center;justify-content:center}

.footer{left:60px;top:2640px;width:1080px;height:128px;background:var(--deep);padding:34px 30px 0}
.footer ul{display:flex;list-style:none;gap:12px;color:#aaa;font-size:11px}
.footer ul li+li::before{content:"|";margin-right:12px;color:#555}
.footer p{color:#777;font-size:10px;margin-top:12px}
.follow{position:absolute;right:30px;top:34px;display:flex;gap:8px;align-items:center;color:#aaa;font-size:11px}
.follow .label{margin-right:6px}
</style>
</head>
<body>

<header class="topbar abs">
  <div class="brand">Vantmere</div>
  <div class="login">
    <svg width="12" height="12" viewBox="0 0 12 12"><circle cx="6" cy="4" r="2.6" fill="#ccc"/><path d="M1 12c0-3 2.2-4.6 5-4.6S11 9 11 12z" fill="#ccc"/></svg>
    Login
  </div>
  <div class="connect">
    <span class="label">Connect With us</span>
    <span class="social-dot"></span><span class="social-dot"></span><span class="social-dot"></span>
  </div>
</header>

<nav class="mainnav abs">
  <ul>
    <li class="active">HOME</li><li>NEWS</li><li>BUSINESS</li><li>MAGAZINE</li><li>VIDEO</li><li>HUMOR</li><li>POLITICAL</li><li>ARCHIVES</li><li>CONTACT</li>
  </ul>
  <div class="donate"><small>Donate with</small><strong>quidlane</strong></div>
  <div class="search">
    <svg width="16" height="16" viewBox="0 0 16 16"><circle cx="6.5" cy="6.5" r="4.8" fill="none" stroke="#1b1b1b" stroke-width="2"/><path d="M10 10l4.5 4.5" stroke="#1b1b1b" stroke-width="2.2" stroke-linecap="round"/></svg>
  </div>
</nav>

<section class="hero abs">
  <div class="photo" role="img" aria-label="Photo of hands using a tablet showing market charts"></div>
  <svg class="hero-arrow" style="left:20px" width="24" height="40" viewBox="0 0 24 40"><path d="M18 4L6 20l12 16" fill="none" stroke="#fff" stroke-width="3"/></svg>
  <svg class="hero-arrow" style="right:20px" width="24" height="40" viewBox="0 0 24 40"><path d="M6 4l12 16L6 36" fill="none" stroke="#fff" stroke-width="3"/></svg>
  <div class="hero-caption">GLOBAL NEWS AROUND THE WORLD</div>
  <div class="hero-dots"><span></span><span></span><span></span><span></span></div>
</section>

<main class="panel abs">

  <div class="section-head" style="left:12px;top:40px;width:728px"><span>NEWS</span></div>

  <article class="feature abs">
    <div class="photo" role="img" aria-label="Video still of a businessman at a desk">
      <svg class="play" width="64" height="64" viewBox="0 0 64 64"><circle cx="32" cy="32" r="30" fill="var(--red)"/><path d="M26 20l18 12-18 12z" fill="#fff"/></svg>
    </div>
    <h3 class="headline">There are many variations of passages of Lorem Ipsum available, but the majority have</h3>
    <div class="meta"><span>Jan 14, 2015</span><span>12</span><span>4</span></div>
    <p class="body-text">It is a long established fact that a reader will be distracted by the readable content of a page when looking at its layout. The point of using plain text is that it has a normal spread of letters.</p>
    <span class="more">Read more</span>
  </article>

  <ul class="news-list abs">
    <li><div class="thumb" role="img" aria-label="Thumbnail photo of a man in a suit" style="background:linear-gradient(150deg,#c8ccd0,#5d6670)"></div>
      <div><h4 class="headline">Contrary to popular belief, Lorem Ipsum is not simply</h4><div class="meta"><span>Jan 14, 2015</span></div></div></li>
    <li><div class="thumb" role="img" aria-label="Thumbnail photo of a business meeting" style="background:linear-gradient(150deg,#d6d9dc,#7b848d)"></div>
      <div><h4 class="headline">There are many variations of passages of Lorem</h4><div class="meta"><span>Jan 14, 2015</span></div></div></li>
    <li><div class="thumb" role="img" aria-label="Thumbnail photo of an office worker" style="background:linear-gradient(150deg,#bfc5cb,#4f5962)"></div>
      <div><h4 class="headline">Sed ut perspiciatis unde omnis iste natus error sit</h4><div class="meta"><span>Jan 14, 2015</span></div></div></li>
    <li><div class="thumb" role="img" aria-label="Thumbnail photo of a man on the phone" style="background:linear-gradient(150deg,#d1c7be,#6b5f56)"></div>
      <div><h4 class="headline">At vero eos et accusamus et iusto odio dignissimos ducimus</h4><div class="meta"><span>Jan 14, 2015</span></div></div></li>
    <li><div class="thumb" role="img" aria-label="Thumbnail photo of a team at a laptop" style="background:linear-gradient(150deg,#cfd4d8,#606a73)"></div>
      <div><h4 class="headline">On the other hand, we denounce with righteous</h4><div class="meta"><span>Jan 14, 2015</span></div></div></li>
  </ul>

  <div class="section-head" style="left:12px;top:688px;width:728px"><span>ARTICLES</span></div>
  <div class="articles abs">
    <div class="article-card"><div class="photo" role="img" aria-label="Photo of a business handshake" style="background:linear-gradient(160deg,#cdd3d8,#3e4c59)"></div>
      <div class="overlay"><span class="tag">Article 1</span><h4 class="headline">But I must explain to you how all this mistaken</h4></div></div>
    <div class="article-card"><div class="photo" role="img" aria-label="Photo of colleagues shaking hands" style="background:linear-gradient(160deg,#d8dde1,#4a5866)"></div>
      <div class="overlay"><span class="tag">Article 2</span><h4 class="headline">Sed ut perspiciatis unde omnis iste natus</h4></div></div>
    <div class="article-card"><div class="photo" role="img" aria-label="Photo of a meeting table" style="background:linear-gradient(160deg,#bcc4cb,#34414e)"></div>
      <div class="overlay"><span class="tag">Article 3</span><h4 class="headline">At vero eos et accusamus et iusto</h4></div></div>
    <div class="article-card"><div class="photo" role="img" aria-label="Photo of an office team" style="background:linear-gradient(160deg,#d0d5da,#45525f)"></div>
      <div class="overlay"><span class="tag">Article 4</span><h4 class="headline">On the other hand, we denounce with</h4></div></div>
  </div>

  <div class="section-head" style="left:12px;top:1020px;width:728px"><span>LATEST NEWS</span></div>
  <div class="latest-main abs photo" role="img" aria-label="Photo of business people walking in an office"></div>
  <article class="latest-copy abs">
    <span class="tag">Our Operation</span>
    <h3 class="headline">On the other hand, we denounce with</h3>
    <div class="meta"><span>Jan 14, 2015</span><span>8</span></div>
    <p class="body-text">It is a long established fact that a reader will be distracted by the readable content of a page when looking at its layout. The point of using plain text is that it reads well.</p>
    <span class="more">Read more</span>
  </article>

  <article class="latest-small abs" style="left:12px;width:360px">
    <div class="photo" role="img" aria-label="Photo of two colleagues talking" style="width:128px;height:100px;background:linear-gradient(150deg,#d7dbdf,#6a747d)"></div>
    <div><h4 class="headline">Contrabelled</h4><p class="body-text">There are many variations of passages of text available to the reader.</p><div class="meta"><span>Jan 14, 2015</span></div></div>
  </article>
  <article class="latest-small abs" style="left:400px;width:340px">
    <div class="photo" role="img" aria-label="Photo of a man in a suit" style="width:104px;height:100px;background:linear-gradient(150deg,#c9ced3,#56606a)"></div>
    <div><h4 class="headline">Who do not know how</h4><p class="body-text">To pursue pleasure rationally encounter consequences that are extremely painful.</p><div class="meta"><span>Jan 14, 2015</span></div></div>
  </article>

  <div class="section-head side" style="left:772px;top:40px;width:300px"><span>TRENDING</span></div>
  <ul class="trending abs">
    <li><span class="bullet"></span><h4 class="headline">There are many variations of passages of Lorem</h4></li>
    <li><span class="bullet"></span><h4 class="headline">On the other hand, we denounce with righteous indignation</h4></li>
    <li><span class="bullet"></span><h4 class="headline">At vero eos et accusamus et iusto odio dignissimos</h4></li>
    <li><span class="bullet"></span><h4 class="headline">But I must explain to you how all this mistaken idea</h4></li>
    <li><span class="bullet"></span><h4 class="headline">Sed ut perspiciatis unde omnis iste natus error</h4></li>
  </ul>

  <div class="section-head side" style="left:772px;top:586px;width:300px"><span>RECENT POST</span></div>
  <ul class="recent abs">
    <li><div class="thumb" role="img" aria-label="Thumbnail photo of a businessman" style="background:linear-gradient(150deg,#cfd4d8,#5a646d)"></div><div><h4 class="headline">We denounce with righteous</h4><div class="meta"><span>Jan 14, 2015</span></div></div></li>
    <li><div class="thumb" role="img" aria-label="Thumbnail photo of an office desk" style="background:linear-gradient(150deg,#d9dcdf,#747d86)"></div><div><h4 class="headline">At vero eos et accusamus et iusto odio</h4><div class="meta"><span>Jan 14, 2015</span></div></div></li>
    <li><div class="thumb" role="img" aria-label="Thumbnail photo of a man smiling" style="background:linear-gradient(150deg,#d3c9c0,#6e6259)"></div><div><h4 class="headline">But I must explain to you how all this mistaken</h4><div class="meta"><span>Jan 14, 2015</span></div></div></li>
    <li><div class="thumb" role="img" aria-label="Thumbnail photo of a woman at work" style="background:linear-gradient(150deg,#c7ccd1,#525c66)"></div><div><h4 class="headline">On the other hand, we denounce</h4><div class="meta"><span>Jan 14, 2015</span></div></div></li>
    <li><div class="thumb" role="img" aria-label="Thumbnail photo of a team meeting" style="background:linear-gradient(150deg,#d5d9dd,#66707a)"></div><div><h4 class="headline">We denounce with righteous</h4><div class="meta"><span>Jan 14, 2015</span></div></div></li>
  </ul>

  <article class="side-card abs" style="top:1036px">
    <div class="photo" role="img" aria-label="Photo of a business presentation" style="height:200px;background:linear-gradient(150deg,#dde1e4,#7f8992 60%,#4a545d)"><span class="tag">Video 1</span></div>
    <h4 class="headline">But I must explain to you how all this mistaken idea</h4>
    <div class="meta"><span>Jan 14, 2015</span></div>
  </article>
  <article class="side-card abs" style="top:1334px">
    <div class="photo" role="img" aria-label="Photo of a man presenting to colleagues" style="height:150px;background:linear-gradient(150deg,#e2e4e6,#8d959c 60%,#545d66)"><span class="tag">Video 2</span></div>
    <h4 class="headline">But I must explain to you how all this mistaken idea</h4>
    <div class="meta"><span>Jan 14, 2015</span></div>
  </article>

  <div class="gallery abs">
    <figure><div class="photo" role="img" aria-label="Photo of a smiling business team" style="background:linear-gradient(160deg,#c4b6a8,#5b4d42 70%,#2f2823)"></div>
      <figcaption><span class="tag">Heading 1</span><h4 class="headline">On the other hand, we denounce with</h4></figcaption></figure>
    <figure><div class="photo" role="img" aria-label="Photo of business people celebrating" style="background:linear-gradient(160deg,#d5d9dd,#6b7680 70%,#36404a)"></div>
      <figcaption><span class="tag">Heading 2</span><h4 class="headline">On the other hand, we denounce with</h4></figcaption></figure>
    <figure><div class="photo" role="img" aria-label="Photo of a team joining hands" style="background:linear-gradient(160deg,#bfc8d0,#4d6070 70%,#25323d)"></div>
      <figcaption><span class="tag">Heading 3</span><h4 class="headline">On the other hand, we denounce with</h4></figcaption></figure>
  </div>
</main>

<section class="newsletter abs">
  <h2>SUBSCRIBE TO OUR NEWSLETTER</h2>
  <div class="subscribe">
    <div class="field">
      <svg width="14" height="10" viewBox="0 0 14 10"><rect x=".5" y=".5" width="13" height="9" fill="none" stroke="#888"/><path d="M.5 .5L7 6l6.5-5.5" fill="none" stroke="#888"/></svg>
      Enter Email Id
    </div>
    <div class="go"><svg width="14" height="14" viewBox="0 0 14 14"><path d="M1 7l12-6-4 12-2-5z" fill="#fff"/></svg></div>
  </div>
</section>

<footer class="footer abs">
  <ul><li>Home</li><li>News</li><li>Business</li><li>Magazine</li><li>Video</li><li>Humor</li><li>Political</li><li>Archives</li></ul>
  <p>Copyright © 2015 All Rights Reserved</p>
  <div class="follow"><span class="label">Follow us on</span><span class="social-dot"></span><span class="social-dot"></span><span class="social-dot"></span></div>
</footer>

</body>
</html>
```